Boutique Store Selling Antiques and Unique Finds

I need a Web Page designed for my Store Called "Willow Lane". I would like a very classic, muted design that looks European when pulled up. I will be selling Antiques from all over the world and Unique finds that have reproduced. I will also be selling high-end purses and jewelry with unique, reasonable products for the every-day buyer as well.

Target Market(s)

25-70 year old men and women;)

Coding

Coded - Design and coding required

Number of Pages Required

1 page

Colors

Designer to choose only greyscale colors for use in the design.

Requirements
Must have
• I want it

```html
<!DOCTYPE html>
<html lang="en">
<head>
<meta charset="utf-8">
<title>Willow Lane — Antiques &amp; Unique Finds</title>
<link href="https://fonts.googleapis.com/css2?family=Cinzel:wght@400;500;700&family=Poppins:wght@300;400;500&family=Lato:wght@400&display=swap" rel="stylesheet">
<style>
:root{
  --ink:#111111;
  --text:#333333;
  --muted:#666666;
  --line:#cfcfcf;
  --soft:#f2f2f2;
  --panel:#eeeeee;
  --footer:#2f2f2f;
  --footer-text:#e6e6e6;
  --price:#e0245e;
  --white:#ffffff;
}
*{margin:0;padding:0;box-sizing:border-box}
html,body{width:1200px;height:3919px;overflow:hidden;background:var(--white)}
body{position:relative;font-family:"Poppins",sans-serif;color:var(--text)}
.abs{position:absolute}

/* header */
.site-header{left:0;top:0;width:1200px;height:137px;background:var(--white)}
.brand{left:172px;top:38px;display:flex;align-items:center;gap:14px}
.brand-dot{width:18px;height:18px;border:2px solid var(--ink);border-radius:50%}
.brand-name{font-family:"Cinzel",serif;font-size:34px;font-weight:500;letter-spacing:5px;color:var(--ink)}
.main-nav{left:589px;top:60px;display:flex;gap:20px;font-size:14px;font-weight:400;color:var(--ink)}
.main-nav a{color:var(--ink);text-decoration:none}
.main-nav a.active{text-decoration:underline;text-underline-offset:5px}
.icon-btn{top:54px;width:36px;height:36px;border:2px solid var(--ink);border-radius:50%;display:flex;align-items:center;justify-content:center}

/* hero */
.hero{left:0;top:137px;width:1200px;height:570px;background:linear-gradient(180deg,#a9a9a9 0%,#c9c9c9 45%,#8f8f8f 100%)}
.hero-art{left:0;top:0;width:1200px;height:570px;background:radial-gradient(ellipse at 40% 65%,#6b5a4d 0%,rgba(107,90,77,0) 45%),radial-gradient(ellipse at 85% 70%,#5a4a42 0%,rgba(90,74,66,0) 30%)}
.hero-title{font-family:"Cinzel",serif;font-weight:500;color:var(--ink);font-size:58px;letter-spacing:6px}
.hero-dots{left:570px;top:534px;display:flex;gap:10px}
.hero-dots span{width:13px;height:13px;border-radius:50%;background:rgba(255,255,255,.5)}
.hero-dots span:first-child{background:var(--white)}

/* promos */
.promo{top:756px;width:418px;height:240px;overflow:hidden}
.promo-light{left:172px;background:var(--panel)}
.promo-dark{left:610px;background:linear-gradient(180deg,#8a8a8a,#5c5c5c)}
.promo-art{position:absolute;left:12px;top:16px;width:200px;height:210px;border-radius:8px}
.promo-body{position:absolute;left:218px;top:30px}
.promo-title{font-family:"Cinzel",serif;font-size:28px;font-weight:500}
.promo-text{font-size:14px;margin-top:10px}
.promo-btn{display:inline-block;margin-top:14px;padding:10px 6px;border:2px solid currentColor;font-size:13px}

/* sections */
.section-title{left:0;width:1200px;text-align:center;font-family:"Cinzel",serif;font-size:44px;font-weight:500;color:var(--ink)}
.section-rule{left:547px;width:106px;height:2px;background:var(--ink)}
.section-sub{left:0;width:1200px;text-align:center;font-size:13px;color:var(--muted)}

.product{width:202px;height:292px;border:2px solid var(--line);text-align:center}
.product-art{width:150px;height:130px;margin:28px auto 0;border-radius:10px}
.product-name{font-family:"Lato",sans-serif;font-size:18px;color:var(--ink);line-height:24px;margin-top:14px}
.product-price{font-family:"Cinzel",serif;font-weight:700;font-size:19px;color:var(--price);margin-top:8px}

/* banner */
.banner{left:0;top:1609px;width:1200px;height:453px;background:linear-gradient(90deg,#5a4638 0%,#3e3530 40%,#4a3e36 70%,#6e6a66 100%)}
.banner-text{left:250px;top:205px;width:700px;text-align:center;font-family:"Cinzel",serif;font-size:38px;line-height:53px;color:var(--white)}

/* blog */
.blog-band{left:0;top:2685px;width:1200px;height:514px;background:var(--soft)}
.post{top:2762px;width:273px;height:356px;background:var(--white);border:2px solid var(--line);text-align:center}
.post-art{width:269px;height:263px}
.post-title{font-family:"Lato",sans-serif;font-size:19px;color:var(--ink);margin-top:16px}
.post-date{font-size:13px;color:var(--muted);margin-top:8px}

/* newsletter */
.news-sub{left:0;top:3343px;width:1200px;text-align:center;font-size:14px;color:var(--ink)}
.news-input{left:332px;top:3433px;width:401px;height:58px;border:2px solid #999;font-size:13px;padding:19px 10px;color:var(--ink)}
.news-btn{left:742px;top:3433px;width:126px;height:58px;background:var(--ink);color:var(--white);font-size:16px;font-weight:500;display:flex;align-items:center;justify-content:center}

/* footer */
.site-footer{left:0;top:3570px;width:1200px;height:349px;background:var(--footer);color:var(--footer-text)}
.footer-col{top:68px;font-size:14px;line-height:26.6px}
.footer-rule{left:172px;top:251px;width:856px;height:1px;background:#777}
.copyright{left:172px;top:290px;font-size:13px}
.pay-strip{left:812px;top:284px;display:flex;gap:4px;background:var(--white);padding:5px 8px}
.pay-strip span{width:24px;height:18px;background:#c7c7c7;border-radius:2px}
</style>
</head>
<body>

<header class="site-header abs">
  <div class="brand abs"><span class="brand-dot"></span><span class="brand-name">Willow Lane</span></div>
  <nav class="main-nav abs">
    <a class="active" href="#">HOME</a><a href="#">ABOUT</a><a href="#">CONTACT</a><a href="#">PRICING</a><a href="#">SHOP</a>
  </nav>
  <div class="icon-btn abs" style="left:945px">
    <svg width="16" height="16" viewBox="0 0 16 16" fill="none" stroke="#111" stroke-width="1.6"><rect x="2.5" y="5" width="11" height="9.5" rx="1"/><path d="M5.5 5V4a2.5 2.5 0 0 1 5 0v1"/></svg>
  </div>
  <div class="icon-btn abs" style="left:990px">
    <svg width="16" height="16" viewBox="0 0 16 16" fill="none" stroke="#111" stroke-width="2"><circle cx="6.5" cy="6.5" r="4.5"/><path d="M10 10l4 4"/></svg>
  </div>
</header>

<section class="hero abs">
  <div class="hero-art abs" role="img" aria-label="Vintage radio, gramophone on a wooden desk, shelves of antiques and a hat stand against a grey plaster wall"></div>
  <div class="hero-title abs" style="left:580px;top:50px">Willow</div>
  <div class="hero-title abs" style="left:740px;top:118px">Lane</div>
  <div class="hero-dots abs"><span></span><span></span><span></span></div>
</section>

<article class="promo promo-light abs">
  <div class="promo-art" role="img" aria-label="Gilded antique mantel clock" style="background:radial-gradient(circle,#b8923e 0%,#8a6a2c 55%,rgba(238,238,238,0) 72%)"></div>
  <div class="promo-body" style="left:218px;color:var(--ink)">
    <div class="promo-title">Antiques</div>
    <div class="promo-text">Duis aute irure dolor nulla</div>
    <div class="promo-btn">READ MORE</div>
  </div>
</article>
<article class="promo promo-dark abs">
  <div class="promo-art" role="img" aria-label="Vintage tabletop radio on a wooden shelf" style="top:70px;height:160px;background:linear-gradient(180deg,#6a5442,#3f3026)"></div>
  <div class="promo-body" style="left:218px;color:var(--white)">
    <div class="promo-title">Unique Finds</div>
    <div class="promo-text">Duis aute irure dolor nulla</div>
    <div class="promo-btn">READ MORE</div>
  </div>
</article>

<h2 class="section-title abs" style="top:1070px">Popular Products</h2>
<div class="section-rule abs" style="top:1145px"></div>
<p class="section-sub abs" style="top:1170px">At vero eos et accusamus et iusto od lorem ipsum gnissimos ducimus bland.</p>

<div class="product abs" style="left:172px;top:1229px"><div class="product-art" role="img" aria-label="Brass and leather telescope" style="background:linear-gradient(150deg,rgba(255,255,255,0) 38%,#5b3a22 45%,#8a5430 55%,rgba(255,255,255,0) 62%)"></div><div class="product-name">Excepteur Sint<br>Occaecat</div><div class="product-price">$50</div></div>
<div class="product abs" style="left:391px;top:1229px"><div class="product-art" role="img" aria-label="Gold cameo brooch" style="background:radial-gradient(ellipse 45px 60px,#e6dccf 60%,#b88a2e 75%,rgba(255,255,255,0) 80%)"></div><div class="product-name">Excepteur Sint<br>Occaecat</div><div class="product-price">$50</div></div>
<div class="product abs" style="left:608px;top:1229px"><div class="product-art" role="img" aria-label="Red velvet armchair with gilded frame" style="background:radial-gradient(ellipse 55px 55px,#b0102a 60%,#c49a4a 72%,rgba(255,255,255,0) 78%)"></div><div class="product-name">Excepteur Sint<br>Occaecat</div><div class="product-price">$50</div></div>
<div class="product abs" style="left:826px;top:1229px"><div class="product-art" role="img" aria-label="Antique wooden coffee grinder" style="background:linear-gradient(180deg,rgba(255,255,255,0) 35%,#6b4a33 45%,#4a3324 100%);width:80px"></div><div class="product-name">Excepteur Sint<br>Occaecat</div><div class="product-price">$50</div></div>

<section class="banner abs" role="img" aria-label="Leather armchairs, a globe and vintage trunks in a brick-walled room">
  <p class="banner-text abs">Antiques from all over the world and Unique finds that have reproduced</p>
</section>

<h2 class="section-title abs" style="top:2137px">Top Products</h2>
<div class="section-rule abs" style="top:2213px"></div>
<p class="section-sub abs" style="top:2238px">At vero eos et accusamus et iusto od lorem ipsum gnissimos ducimus bland.</p>

<div class="product abs" style="left:172px;top:2297px"><div class="product-art" role="img" aria-label="Quilted beige leather handbag" style="background:radial-gradient(ellipse 60px 50px at 50% 60%,#cdb08a 70%,rgba(255,255,255,0) 75%)"></div><div class="product-name" style="margin-top:22px">High-end Purses</div><div class="product-price">$50</div></div>
<div class="product abs" style="left:391px;top:2297px"><div class="product-art" role="img" aria-label="Antique gold necklace with green stones and pearls" style="background:radial-gradient(ellipse 70px 45px,#c9a552 40%,#3c8f7a 55%,rgba(255,255,255,0) 72%)"></div><div class="product-name" style="margin-top:22px">Unique Jewelry</div><div class="product-price">$50</div></div>
<div class="product abs" style="left:608px;top:2297px"><div class="product-art" role="img" aria-label="Tan leather shoulder bag" style="background:radial-gradient(ellipse 65px 45px at 50% 65%,#b88a5c 70%,rgba(255,255,255,0) 75%)"></div><div class="product-name" style="margin-top:22px">High-end Purses</div><div class="product-price">$50</div></div>
<div class="product abs" style="left:826px;top:2297px"><div class="product-art" role="img" aria-label="Gold ring with a large blue gemstone" style="background:radial-gradient(circle 45px,#2f7fd0 50%,#d4a744 70%,rgba(255,255,255,0) 78%)"></div><div class="product-name" style="margin-top:22px">Unique Jewelry</div><div class="product-price">$50</div></div>

<div class="blog-band abs"></div>
<article class="post abs" style="left:172px"><div class="post-art" role="img" aria-label="Gold star crown resting on old books" style="background:linear-gradient(180deg,#cfc6b8 0%,#9c7a3f 45%,#6b3a28 100%)"></div><div class="post-title">Dolore magna aliqua</div><div class="post-date">14 January, 2020</div></article>
<article class="post abs" style="left:464px"><div class="post-art" role="img" aria-label="Jewelled gold crown on a dark stand" style="background:linear-gradient(180deg,#4a3c28 0%,#a88650 50%,#2a2622 100%)"></div><div class="post-title">Dolore magna aliqua</div><div class="post-date">14 January, 2020</div></article>
<article class="post abs" style="left:754px"><div class="post-art" role="img" aria-label="Ornate dark crown with coloured jewels" style="background:linear-gradient(180deg,#c8bfb0 0%,#5a4a36 50%,#3a3a3a 100%)"></div><div class="post-title">Dolore magna aliqua</div><div class="post-date">14 January, 2020</div></article>

<h2 class="section-title abs" style="top:3280px;font-size:40px">Subscribe To Our Newsletter</h2>
<p class="news-sub abs">Sign up for our email list and get 15% off your first order</p>
<div class="section-rule abs" style="top:3386px;left:567px;width:66px;background:#666"></div>
<div class="news-input abs">Email Address</div>
<div class="news-btn abs">Subscribe</div>

<footer class="site-footer abs">
  <div class="footer-col abs" style="left:172px">Return Policy<br>Search<br>Blog<br>Contact us<br>About us</div>
  <div class="footer-col abs" style="left:412px">Home<br>About<br>Blog<br>Pricing<br>Contact</div>
  <div class="footer-col abs" style="left:630px">Nemo enim ipsam<br>Voluptatem quia<br>Voluptas sit<br>Aspernatur aut odit<br>Aut fugit</div>
  <div class="footer-col abs" style="left:896px">Nemo enim ipsam<br>Voluptatem quia<br>Voluptas sit<br>Aspernatur aut odit<br>Aut fugit</div>
  <div class="footer-rule abs"></div>
  <div class="copyright abs">Copyrights @ 2021 Willow Lane. All Rights Reserved.</div>
  <div class="pay-strip abs"><span></span><span></span><span></span><span></span><span></span><span></span><span></span></div>
</footer>

</body>
</html>
```